zAvora Corporate Website

zAvora is a well-funded start up developing an Online Marketing Platform for small businesses in Europe.
We are launching in February 2012 with all-in-one online marketing services including professional website, DIY SEO, Dashboard with Reports and Online marketing tools, and Support.
Our internal web designer has come up with a preliminary website design which we wish to continue to improve using new ideas, colours, layout, image, etc.
The brief is very simple - improve the website whether it is look & feel, ease of use, conversion rate - we are looking for overall improvements.
The contest will last 5 days and we will award the winner £300.
If you are the winner , you will also be required to provide designs for 3 more internal pages adhering to the proposed home page design.
Judging criteria : -
Visual Design
Layout must adhere to best practices and wire frame. If you decide to move elements around significantly please provide reason
Functional, informative and drives calls to action
Industry/Entity Type
Marketing
Look and feel
Each slider illustrates characteristics of the customer's brand and the style your logo design should communicate.

```html
<!DOCTYPE html>
<html lang="en">
<head>
<meta charset="utf-8">
<title>zAvora – Online Marketing Platform</title>
<link rel="stylesheet" href="https://fonts.googleapis.com/css2?family=Carlito:wght@400;700&family=Open+Sans:wght@400;600&display=swap">
<style>
  :root {
    --page: #f7f7f7;
    --white: #ffffff;
    --ink: #333333;
    --ink-soft: #555555;
    --muted: #666666;
    --sky: #5bc8e8;
    --sky-deep: #27b4e3;
    --sky-text: #4fc3e6;
    --charcoal: #3f3f3f;
    --charcoal-light: #6a6a6a;
    --line: #d7d7d7;
  }
  * { box-sizing: border-box; margin: 0; padding: 0; }
  html, body { width: 1151px; height: 1200px; overflow: hidden; }
  body {
    position: relative;
    background: var(--page);
    font-family: "Open Sans", Arial, sans-serif;
    color: var(--ink);
  }
  .abs { position: absolute; }

  /* top strip */
  .topbar {
    left: 0; top: 0; width: 1151px; height: 27px;
    background: linear-gradient(#5a5a5a, #3a3a3a);
  }
  .account-links {
    right: 60px; top: 6px; font-size: 13px; color: var(--white);
    font-family: "Carlito", sans-serif; font-size: 14px;
  }
  .account-links span { margin: 0 4px; }

  /* brand */
  .brand { left: 71px; top: 80px; display: flex; align-items: center; gap: 10px; }
  .brand-dot { width: 42px; height: 42px; border-radius: 50%; background: var(--sky-deep); }
  .brand-name {
    font-family: "Open Sans", sans-serif; font-size: 37px; font-weight: 400;
    color: var(--ink-soft); line-height: 1;
  }

  /* search */
  .search {
    left: 873px; top: 52px; width: 219px; height: 29px;
    background: var(--white); border: 1px solid #bdbdbd;
    font-family: "Carlito", sans-serif; font-style: italic; font-size: 15px;
    color: var(--ink-soft); padding: 5px 0 0 18px;
  }
  .search svg { position: absolute; right: 6px; top: 4px; }

  /* nav */
  .main-nav {
    left: 590px; top: 99px; width: 509px; height: 32px;
    background: linear-gradient(#777, #3c3c3c 55%, #2e2e2e);
    border-radius: 12px; border: 1px solid #2a2a2a;
    display: flex; align-items: center; padding-left: 18px;
  }
  .main-nav a {
    font-family: "Carlito", sans-serif; font-size: 15px; color: var(--white);
    text-decoration: none; height: 100%; display: flex; align-items: center; justify-content: center;
  }
  .main-nav .is-active {
    width: 104px; background: linear-gradient(#4fd0f4, #16a6d8); color: #0a4f6a;
  }
  .main-nav .item { width: 125px; border-left: 1px solid transparent; position: relative; }
  .main-nav .item + .item::before {
    content: ""; position: absolute; left: 0; top: 8px; height: 16px; border-left: 1px solid #111;
  }

  /* hero slider */
  .hero-shadow {
    left: 0; top: 470px; width: 1151px; height: 110px;
    background: radial-gradient(ellipse at 50% 0%, rgba(0,0,0,0.45), rgba(0,0,0,0) 65%);
  }
  .hero {
    left: 62px; top: 158px; width: 1031px; height: 384px;
    background: var(--white);
    box-shadow: 0 6px 14px rgba(0,0,0,0.2);
  }
  .hero-art {
    left: 37px; top: 28px; width: 427px; height: 318px;
    background: radial-gradient(ellipse at 40% 45%, #f0b84a 0%, #d9d9d9 38%, #f2f2f2 70%, #ffffff 100%);
  }
  .hero-title {
    left: 501px; top: 40px; width: 510px;
    font-family: "Carlito", sans-serif; font-size: 36px; line-height: 44px; color: var(--ink);
  }
  .hero-sub {
    left: 501px; top: 130px; width: 510px;
    font-family: "Carlito", sans-serif; font-size: 25px; line-height: 44px; color: var(--sky-text);
  }
  .hero-copy {
    left: 506px; top: 227px; width: 460px;
    font-size: 13px; line-height: 26px; color: var(--ink);
  }
  .hero-copy span { margin-right: 10px; }
  .btn-more {
    left: 866px; top: 318px; width: 86px; height: 26px;
    background: linear-gradient(#3fd1f5, #13abd9); border: 2px solid #8fe3f7;
    border-radius: 10px; color: var(--white); font-size: 11px;
    display: flex; align-items: center; justify-content: center;
  }
  .slide-arrow {
    top: 324px; width: 35px; height: 35px; background: var(--charcoal);
    border-radius: 3px; display: flex; align-items: center; justify-content: center;
  }
  .slide-arrow.prev { left: 60px; }
  .slide-arrow.next { left: 1057px; }

  /* announcement */
  .announce {
    left: 57px; top: 578px; width: 1044px; height: 70px;
    background: var(--sky); border: 1px solid #3aa6c8;
    font-family: "Carlito", sans-serif; font-size: 25px; color: var(--white);
    display: flex; align-items: center; justify-content: center;
  }

  /* welcome */
  .welcome-title {
    left: 82px; top: 674px; font-family: "Carlito", sans-serif; font-size: 25px; color: #111;
  }
  .welcome-copy {
    left: 84px; top: 717px; width: 680px;
    font-size: 11px; line-height: 26.4px; color: var(--muted);
  }

  /* service cards */
  .service {
    top: 871px; width: 228px; height: 160px; border-radius: 10px;
    overflow: hidden; background: var(--white);
    box-shadow: 0 2px 6px rgba(0,0,0,0.08);
  }
  .service-head {
    height: 33px; background: var(--sky); color: #333;
    font-family: "Carlito", sans-serif; font-size: 15px;
    display: flex; align-items: center; justify-content: center; border-bottom: 1px solid #e8e8e8;
  }
  .service-art { height: 127px; }
  .art-design { background: linear-gradient(120deg, #2aa3dc 0%, #e9e9e9 45%, #c9b6a8 75%, #ffffff 100%); }
  .art-publish { background: radial-gradient(circle at 45% 50%, #ffffff 0 12%, #3cb4e6 13% 38%, #e14a8a 55%, #222 80%, #ffffff 100%); }
  .art-promote { background: linear-gradient(200deg, #ffffff 0%, #f3f3f3 40%, #7cc540 65%, #3a8f2a 100%); }

  /* news */
  .news {
    left: 854px; top: 680px; width: 247px; height: 407px;
    background: var(--white); border: 1px solid var(--line); border-radius: 12px;
  }
  .news-head {
    left: 854px; top: 681px; width: 247px; height: 37px;
    background: linear-gradient(#5c5c5c, #333); border-radius: 14px 14px 0 0;
    color: var(--white); font-family: "Carlito", sans-serif; font-size: 18px;
    padding: 8px 0 0 62px;
  }
  .news-icon {
    left: 841px; top: 671px; width: 60px; height: 60px; border-radius: 50%;
    background: radial-gradient(circle at 40% 35%, #ffffff, #dcdcdc);
    border: 1px solid #c8c8c8; display: flex; align-items: center; justify-content: center;
  }
  .badge { background: #dcdde2; border: 1px solid #c7c8cf; }
  .badge-a { left: 888px; top: 752px; width: 82px; height: 100px; }
  .badge-b { left: 948px; top: 743px; width: 82px; height: 100px; background: #e4e5ea; }
  .badge-c { left: 882px; top: 895px; width: 168px; height: 76px; background: #ececec; }
  .news-text { font-size: 11px; color: var(--muted); }
  .news-years-1 { left: 890px; top: 862px; }
  .news-final { left: 891px; top: 963px; line-height: 16px; }
  .news-copy { left: 891px; top: 1004px; width: 196px; font-size: 10.5px; line-height: 27px; }

  /* footer */
  .footer {
    left: 0; top: 1117px; width: 1151px; height: 83px;
    background: linear-gradient(#3a3a3a, #5e5e5e);
  }
  .footer-dot {
    left: 72px; top: 1137px; width: 42px; height: 42px; border-radius: 50%;
    background: #d8d8d8;
  }
  .footer-links { left: 130px; top: 1138px; font-size: 11px; color: var(--white); }
  .footer-links a { color: var(--white); text-decoration: none; margin-right: 8px; }
  .copyright { left: 130px; top: 1165px; font-size: 11px; color: var(--white); }
  .connect { left: 828px; top: 1139px; font-size: 11px; color: var(--white); }
  .social {
    top: 1130px; width: 33px; height: 33px; border-radius: 50%;
    box-shadow: inset 0 -3px 5px rgba(0,0,0,0.3);
  }
  .social.s1 { left: 930px; background: #2f4c8a; }
  .social.s2 { left: 970px; background: #dcdcdc; }
  .social.s3 { left: 1009px; background: #a51c22; }
  .social.s4 { left: 1050px; background: #8fc3d8; }
</style>
</head>
<body>
  <header>
    <div class="abs topbar"></div>
    <div class="abs account-links">Login <span>|</span> Register</div>

    <div class="abs brand">
      <div class="brand-dot"></div>
      <div class="brand-name">zAvora</div>
    </div>

    <div class="abs search">Search...
      <svg width="22" height="22" viewBox="0 0 22 22" aria-hidden="true">
        <circle cx="9" cy="9" r="6.5" fill="none" stroke="#8a8a8a" stroke-width="2"/>
        <line x1="14" y1="14" x2="20" y2="20" stroke="#8a8a8a" stroke-width="2.5" stroke-linecap="round"/>
      </svg>
    </div>

    <nav class="abs main-nav">
      <a class="is-active" href="#">Home</a>
      <a class="item" href="#">Products</a>
      <a class="item" href="#">About Us</a>
      <a class="item" href="#">Contact Us</a>
    </nav>
  </header>

  <section>
    <div class="abs hero-shadow"></div>
    <div class="abs hero">
      <div class="abs hero-art" role="img" aria-label="Illustration of small gold figures walking hand in hand up an arrow rising over silver bar-chart steps"></div>
      <h1 class="abs hero-title" style="font-weight:400">Online Marketing Platform for Small Business</h1>
      <p class="abs hero-sub">Cloud technology, high automation and our web expertise make it all possible.</p>
      <p class="abs hero-copy"><span>We set up everything in 3 hours</span> <span>You manage it-15 mins per week</span> We provide full support</p>
      <div class="abs btn-more">View More</div>
    </div>
    <div class="abs slide-arrow prev">
      <svg width="12" height="14" viewBox="0 0 12 14" aria-hidden="true"><polyline points="8,2 3,7 8,12" fill="none" stroke="#5bc8e8" stroke-width="2"/></svg>
    </div>
    <div class="abs slide-arrow next">
      <svg width="12" height="14" viewBox="0 0 12 14" aria-hidden="true"><polyline points="4,2 9,7 4,12" fill="none" stroke="#5bc8e8" stroke-width="2"/></svg>
    </div>
  </section>

  <div class="abs announce">We are launching a product that will revolutionize online marketing for SME's</div>

  <main>
    <h2 class="abs welcome-title" style="font-weight:400">Welcome To Our Site</h2>
    <p class="abs welcome-copy">Lorem Ipsum is simply dummy text of the printing and typesetting industry. Lorem Ipsum has been the industry's standard dummy text ever since the 1500s, when an unknown printer took a galley of type and scrambled it to make a type specimen book. It has survived not only five centuries, but also the leap into electronic typesetting, remaining essentially unchanged. It was popularised in the 1960s with the release of Lettrex sheets containing Lorem Ipsum passages, and more recently with desktop publishing software like Folio PageSet including versions of Lorem Ipsum.</p>

    <div class="abs service" style="left:88px">
      <div class="service-head">WEB SITE DESIGN</div>
      <div class="service-art art-design" role="img" aria-label="Illustration of a hand sketching a website on a monitor with blue splashes"></div>
    </div>
    <div class="abs service" style="left:342px">
      <div class="service-head">PUBLISH</div>
      <div class="service-art art-publish" role="img" aria-label="Colourful abstract circles and graphic shapes illustrating publishing"></div>
    </div>
    <div class="abs service" style="left:590px">
      <div class="service-head">PROMOTE</div>
      <div class="service-art art-promote" role="img" aria-label="Green pen ticking boxes on a checklist"></div>
    </div>
  </main>

  <aside>
    <div class="abs news"></div>
    <div class="abs news-head">LATEST NEWS</div>
    <div class="abs news-icon">
      <svg width="30" height="30" viewBox="0 0 30 30" aria-hidden="true">
        <rect x="5" y="6" width="18" height="20" rx="2" fill="#fff" stroke="#9a9a9a"/>
        <line x1="8" y1="12" x2="19" y2="12" stroke="#b5b5b5"/>
        <line x1="8" y1="16" x2="19" y2="16" stroke="#b5b5b5"/>
        <line x1="8" y1="20" x2="16" y2="20" stroke="#b5b5b5"/>
        <line x1="14" y1="22" x2="26" y2="6" stroke="#e0871f" stroke-width="3" stroke-linecap="round"/>
      </svg>
    </div>
    <div class="abs badge badge-a"></div>
    <div class="abs badge badge-b"></div>
    <div class="abs news-text news-years-1">2004, 2005, 2007, 2008</div>
    <div class="abs badge badge-c"></div>
    <div class="abs news-text news-final">Finalist<br>2004, 2005, 2006, 2009, 2010</div>
    <p class="abs news-text news-copy">Lorem Ipsum is simply dummy text of the printing and typesetting industry.</p>
  </aside>

  <footer>
    <div class="abs footer"></div>
    <div class="abs footer-dot"></div>
    <nav class="abs footer-links">
      <a href="#">Site Map</a><a href="#">Home</a><a href="#">About Us</a><a href="#">Products</a><a href="#">Contact Us</a>
    </nav>
    <div class="abs copyright">Cop;yright@2011</div>
    <div class="abs connect">Connect With Us:</div>
    <div class="abs social s1"></div>
    <div class="abs social s2"></div>
    <div class="abs social s3"></div>
    <div class="abs social s4"></div>
  </footer>
</body>
</html>
```